Direct to Consumer extended service contract business with a new disruptive business model needs a

We need a customized wordpress design for a company called 'Bright Harbor Assurance'.
We provide an innovative and unique service contract protection program direct to consumers. This program provides monthly coverage for all electronics purchased in the last 4 years and all electronics the consumer purchases in the future for a low monthly fee. The overall design should communicate a sense of legitimacy, ethics, and superior customer service and support (in an industry that has a huge PR issue to overcome).
Electronics is the first product group, other product groups with different price points to launch in the future..

Target Market(s)

All purchasers of electronic goods...all demographics

Industry/Entity Type

Electronics

Font styles to use
Sans Serif

Requirements
Must have
• Customer Testimonials
Industry News
Customer ratings
Blog posts
Call to action messaging
Like the functional elements and design of quillmesa.example (need to be better)
Nice to have
• Like to see video testimonials
Social network "whats trending related to electronics or service contract industry"
Easy way to register products for warranty

```html
<!DOCTYPE html>
<html lang="en">
<head>
<meta charset="utf-8">
<title>Bright Harbor Assurance</title>
<link href="https://fonts.googleapis.com/css2?family=Lato:wght@400;700;900&display=swap" rel="stylesheet">
<style>
:root{
  --green:#0c8a3e;
  --green-dark:#07752f;
  --ink:#222;
  --muted:#555;
  --light:#f4f4f4;
  --line:#e2e2e2;
  --dark-band:#262626;
  --white:#fff;
}
*{box-sizing:border-box;margin:0;padding:0}
html,body{width:1200px;height:3422px;overflow:hidden}
body{font-family:"Lato",Arial,sans-serif;color:var(--ink);background:var(--white);font-size:13px;line-height:1.5}
.wrap{width:860px;margin:0 auto;position:relative}
.btn{display:inline-block;background:var(--green);color:var(--white);font-weight:700;text-transform:uppercase;text-decoration:none;white-space:nowrap}
.sec-title{text-align:center;font-size:21px;font-weight:400;letter-spacing:.5px;text-transform:uppercase}

/* top bar & header */
.topbar{height:37px;background:var(--light);position:relative}
.topbar .tab{position:absolute;left:686px;width:366px;height:37px;background:var(--green);color:var(--white);display:flex;align-items:center;justify-content:space-between;padding:0 22px 0 28px;font-size:14px}
.topbar .tab span{display:flex;align-items:center;gap:8px}
.topbar .links{font-size:12px;letter-spacing:.5px}
.header{height:77px;background:var(--light)}
.header .wrap{display:flex;justify-content:space-between;align-items:center;height:77px}
.logo{font-size:28px;font-weight:900;color:var(--green);letter-spacing:1px}
.nav{display:flex;gap:34px;font-size:15px;text-transform:uppercase}
.nav a{color:var(--ink);text-decoration:none}
.nav a.active{color:var(--green)}

/* hero */
.hero{height:534px;background:linear-gradient(135deg,#cfcfcf,#8f8f8f 60%,#b9b9b9);position:relative}
.hero-device{position:absolute;left:720px;top:60px;width:360px;height:420px;background:linear-gradient(160deg,#d8d8d8,#7b7b7b)}
.video-card{position:absolute;left:172px;top:87px;width:494px;height:378px}
.video-card .media{height:222px;background:linear-gradient(135deg,#c9d8e6,#e9d4bf);position:relative}
.play{position:absolute;left:50%;top:50%;width:84px;height:84px;margin:-42px 0 0 -42px;border-radius:50%;border:5px solid var(--green);display:flex;align-items:center;justify-content:center}
.video-card .caption{height:156px;background:#1f1f1f;color:var(--white);text-align:center;padding-top:14px}
.caption p{font-size:14px;white-space:nowrap}
.caption .btn{margin:12px 0 12px;padding:14px 18px;font-size:17px}

.dots{position:absolute;right:172px;bottom:22px;display:flex;gap:6px}
.dots i{width:16px;height:5px;background:#333;display:block}

/* cta band */
.cta{height:121px;background:var(--dark-band)}
.cta .wrap{display:flex;align-items:center;justify-content:space-between;height:121px;padding:0 38px}
.cta h2{color:var(--white);font-size:22px;font-weight:400;white-space:nowrap}
.cta .btn{width:220px;text-align:center;padding:17px 0;font-size:24px}

/* features */
.features{height:267px;background:var(--light);padding-top:34px}
.features .wrap{display:flex;justify-content:space-between}
.feature{width:268px}
.feature .box{height:108px;background:var(--white);border:1px solid var(--line);display:flex;align-items:center;padding:0 16px;gap:18px}
.feature h3{font-size:15px;font-weight:400;text-transform:uppercase;line-height:1.35}
.feature ul{list-style:none;margin-top:14px;font-size:11.5px}
.feature li{padding-left:16px;position:relative;margin-bottom:8px}
.feature li:before{content:"›";position:absolute;left:3px;color:var(--green);font-weight:900}

/* ratings */
.ratings{height:465px;padding-top:30px}
.cards3{display:flex;justify-content:space-between;margin-top:30px}
.rating{width:268px;text-align:center}
.avatar{width:130px;height:130px;border-radius:50%;margin:0 auto;border:4px solid #eee}
.stars{display:flex;gap:5px;justify-content:center;margin:20px 0 26px}
.rating .name{color:var(--green);font-size:14px}
.rating p{font-size:12px;color:var(--muted);margin:6px 0 16px}
.rating .btn{font-size:11px;padding:7px 18px;font-weight:400}

/* news */
.news{height:517px;background:var(--light);padding-top:28px}
.arrow-row{position:absolute;top:4px;left:0;right:0;display:flex;justify-content:space-between}
.news-card{width:276px}
.thumb{height:148px}
.news-card .tag{display:flex;align-items:center;gap:6px;font-size:11px;margin-top:10px}
.tag i{width:15px;height:12px;background:var(--green);display:block}
.news-card .date{font-size:11px}
.news-card h4{font-size:13px;font-weight:700;margin-top:6px;line-height:1.4}
.news-card p{font-size:11px;color:var(--muted);margin-top:4px;line-height:1.75}
.news-card .btn{font-size:10px;padding:7px 10px;margin-top:16px;font-weight:400}

/* testimonials */
.testimonials{height:334px;background:var(--green);color:var(--white);padding-top:30px}
.testimonials .sec-title{color:var(--white)}
.testimonials .cards3{margin-top:24px}
.vid{width:264px;text-align:center}
.vid .thumb{height:143px;position:relative}
.vid .play{width:52px;height:52px;margin:-26px 0 0 -26px;border:3px solid rgba(255,255,255,.8)}
.vid .who{margin-top:12px;font-size:14px;line-height:1.3}
.vid .who b{display:block}
.side-arrow{position:absolute;top:70px}

/* blog */
.blog{height:467px;background:var(--light);padding-top:30px}
.blog .cards3{margin-top:26px}
.post{width:276px}
.post .thumb{height:148px;position:relative}
.socials{position:absolute;left:10px;top:0;display:flex;flex-direction:column;gap:2px}
.socials i{width:16px;height:16px;background:var(--green);display:block}
.post h4{color:var(--green);font-size:11.5px;font-weight:700;margin-top:10px;line-height:1.5}
.post p{font-size:11px;color:var(--muted);line-height:1.75}
.post .meta{display:flex;align-items:center;gap:14px;margin-top:14px;font-size:11px}
.post .meta span{display:flex;align-items:center;gap:5px}
.post .btn{font-size:11px;padding:7px 14px;font-weight:400}

/* messaging */
.messaging{height:151px;text-align:center;padding-top:30px}
.messaging p{font-size:14px}
.messaging .btn{margin-top:18px;width:198px;padding:7px 0;font-size:13px;font-weight:400}

/* social posts */
.socialposts{height:348px;background:var(--light);padding-top:48px}
.socialposts h2{color:var(--green);font-size:19px;font-weight:400;text-transform:uppercase}
.sp-dots{position:absolute;right:0;top:8px;display:flex;gap:6px}
.sp-dots i{width:13px;height:13px;border-radius:50%;background:#555;display:block}
.sp-dots i:first-child{background:var(--green)}
.sp-post{display:flex;margin-top:34px}
.sp-brand{width:150px;padding-top:50px;font-size:19px;font-weight:700;color:var(--ink)}
.sp-body{width:700px;font-size:15px;color:var(--muted)}
.sp-body .date{font-size:12px;color:var(--ink)}
.sp-author{display:flex;align-items:center;gap:12px;margin-top:24px;font-size:14px;color:var(--ink)}
.sp-author .avatar{width:58px;height:58px;border-width:3px;border-color:var(--green);margin:0}

/* footer */
.footer{height:104px;padding-top:26px}
.footer nav{font-size:11px;text-transform:uppercase}
.footer nav span{margin:0 10px;color:#999}
.footer small{display:block;margin-top:14px;font-size:11px}
.footer .social-dot{position:absolute;right:150px;top:12px;width:28px;height:28px;border-radius:50%;background:#111}
</style>
</head>
<body>

<div class="topbar">
  <div class="tab">
    <span><svg width="18" height="18" viewBox="0 0 24 24"><circle cx="12" cy="12" r="11" fill="none" stroke="#fff" stroke-width="2"/><path d="M8 6.5l2 2-1.2 1.6a8 8 0 0 0 5.1 5.1l1.6-1.2 2 2-1.5 1.8C11 17.3 6.7 13 6.2 8z" fill="#fff"/></svg>855-555-0142</span>
    <span class="links">LOGIN &nbsp;|&nbsp; SUPPORT</span>
  </div>
</div>

<header class="header">
  <div class="wrap">
    <div class="logo">BRIGHT HARBOR</div>
    <nav class="nav">
      <a class="active" href="#">Home</a><a href="#">Plans</a><a href="#">Benefits</a><a href="#">FAQs</a><a href="#">About Us</a>
    </nav>
  </div>
</header>

<section class="hero">
  <div class="hero-device" role="img" aria-label="Hands holding a smartphone showing the company name"></div>
  <div class="video-card">
    <div class="media" role="img" aria-label="Family gathered around a laptop on a sofa">
      <div class="play"><svg width="30" height="34" viewBox="0 0 30 34"><path d="M4 2l24 15L4 32z" fill="#0c8a3e"/></svg></div>
    </div>
    <div class="caption">
      <p>The Days of buying Expensive In-Store Service Plans are Over !</p>
      <a class="btn" href="#">Dont buy anymore in- store service plans</a>
      <p>Bright Harbor Assurance is the solution</p>
    </div>
  </div>
  <div class="dots"><i></i><i></i><i></i><i></i></div>
</section>

<section class="cta">
  <div class="wrap">
    <h2>GET YOUR BRIGHT HARBOR ASSURANCE TODAY !</h2>
    <a class="btn" href="#">Sign Up</a>
  </div>
</section>

<section class="features">
  <div class="wrap">
    <div class="feature">
      <div class="box">
        <svg width="84" height="80" viewBox="0 0 84 80"><path d="M6 44a36 36 0 0 1 72 0c-5-5-11-5-15 0-4-5-11-5-15 0-4-5-11-5-15 0-4-5-11-5-15 0z" fill="#0c8a3e"/><path d="M42 44v24a6 6 0 0 1-12 0" fill="none" stroke="#0c8a3e" stroke-width="4"/><path d="M30 6v6M42 2v6M54 6v6" stroke="#0c8a3e" stroke-width="3"/></svg>
        <h3>Supreior<br>Coverage</h3>
      </div>
      <ul><li>One plan covers all electronic products</li><li>Thousands of Eligible products</li><li>Register any brand from any retailer</li></ul>
    </div>
    <div class="feature">
      <div class="box">
        <svg width="76" height="84" viewBox="0 0 76 84"><path d="M38 4l30 10v24c0 20-13 34-30 42C21 72 8 58 8 38V14z" fill="none" stroke="#0c8a3e" stroke-width="6"/><path d="M22 42l12 12 22-26" fill="none" stroke="#0c8a3e" stroke-width="8"/></svg>
        <h3>Revolutionary<br>Protection</h3>
      </div>
      <ul><li>Repair, Replace or Refund</li><li>Cover past, present and future purchases</li><li>Coverage never ends</li></ul>
    </div>
    <div class="feature">
      <div class="box">
        <svg width="84" height="76" viewBox="0 0 84 76"><circle cx="42" cy="40" r="26" fill="#0c8a3e"/><path d="M10 40a32 32 0 0 1 64 0" fill="none" stroke="#0c8a3e" stroke-width="6"/><rect x="4" y="34" width="12" height="20" rx="4" fill="#0c8a3e"/><rect x="68" y="34" width="12" height="20" rx="4" fill="#0c8a3e"/><path d="M70 54c0 10-10 16-22 16" fill="none" stroke="#0c8a3e" stroke-width="4"/></svg>
        <h3>Revolutionary<br>Protection</h3>
      </div>
      <ul><li>24 hr. customer Hotline</li><li>Over 10,000 service centers</li><li>No questions asked</li></ul>
    </div>
  </div>
</section>

<section class="ratings">
  <h2 class="sec-title">Customer Ratings</h2>
  <div class="wrap cards3">
    <div class="rating">
      <div class="avatar" role="img" aria-label="Portrait of a customer" style="background:linear-gradient(#e8e8e8,#9a8b80)"></div>
      <div class="stars"><svg width="130" height="22" viewBox="0 0 130 22"><g fill="#0c8a3e"><path id="s" d="M11 1l3 7h7l-6 5 2 8-6-4-6 4 2-8-6-5h7z"/><use href="#s" x="27"/><use href="#s" x="54"/><use href="#s" x="81"/><use href="#s" x="108"/></g></svg></div>
      <div class="name">Dana Whitlock</div>
      <p>Lorem Ipsum is simply dummy text of the printing and typesetting industry.</p>
      <a class="btn" href="#">Read More &gt;&gt;</a>
    </div>
    <div class="rating">
      <div class="avatar" role="img" aria-label="Portrait of a customer" style="background:linear-gradient(#d9e87a,#c89a6a)"></div>
      <div class="stars"><svg width="130" height="22" viewBox="0 0 130 22"><g fill="#0c8a3e"><use href="#s"/><use href="#s" x="27"/><use href="#s" x="54"/><use href="#s" x="81"/></g><path d="M119 1l3 7h7l-6 5 2 8-6-4z" fill="#ccc"/><path d="M119 1l-3 7h-7l6 5-2 8 6-4z" fill="#0c8a3e"/></svg></div>
      <div class="name">Dana Whitlock</div>
      <p>Lorem Ipsum is simply dummy text of the printing and typesetting industry.</p>
      <a class="btn" href="#">Read More &gt;&gt;</a>
    </div>
    <div class="rating">
      <div class="avatar" role="img" aria-label="Portrait of a customer" style="background:linear-gradient(#eeeeee,#8a7a72)"></div>
      <div class="stars"><svg width="130" height="22" viewBox="0 0 130 22"><g fill="#0c8a3e"><use href="#s"/><use href="#s" x="27"/><use href="#s" x="54"/><use href="#s" x="81"/><use href="#s" x="108"/></g></svg></div>
      <div class="name">Dana Whitlock</div>
      <p>Lorem Ipsum is simply dummy text of the printing and typesetting industry.</p>
      <a class="btn" href="#">Read More &gt;&gt;</a>
    </div>
  </div>
</section>

<section class="news">
  <div class="wrap">
    <div class="arrow-row"><svg width="10" height="14" viewBox="0 0 10 14"><path d="M8 1L2 7l6 6" fill="none" stroke="#555" stroke-width="2"/></svg><svg width="10" height="14" viewBox="0 0 10 14"><path d="M2 1l6 6-6 6" fill="none" stroke="#555" stroke-width="2"/></svg></div>
    <h2 class="sec-title">Industry News</h2>
    <div class="cards3">
      <article class="news-card">
        <div class="thumb" role="img" aria-label="Hand touching a digital screen" style="background:linear-gradient(135deg,#2a2a2a,#b0784a)"></div>
        <div class="tag"><i></i>NEWS</div>
        <div class="date">Date Posted on 29-08-2014</div>
        <h4>Lorem Ipsum is simply dummy text of the printing and typesetting industry.</h4>
        <p>Lorem Ipsum has been the industry's standard dummy text ever since the 1500s, when an unknown printer took a galley of type and scrambled it to make a type specimen book.</p>
        <a class="btn" href="#">Read More News &gt;&gt;</a>
      </article>
      <article class="news-card">
        <div class="thumb" role="img" aria-label="Technician working on electronics in a lab" style="background:linear-gradient(135deg,#1d3f8a,#c9d4e8)"></div>
        <div class="tag"><i></i>NEWS</div>
        <div class="date">Date Posted on 29-08-2014</div>
        <h4>Lorem Ipsum is simply dummy text of the printing and typesetting industry.</h4>
        <p>Lorem Ipsum has been the industry's standard dummy text ever since the 1500s, when an unknown printer took a galley of type and scrambled it to make a type specimen book.</p>
        <a class="btn" href="#">Read More News &gt;&gt;</a>
      </article>
      <article class="news-card">
        <div class="thumb" role="img" aria-label="Engineer inspecting circuit equipment" style="background:linear-gradient(135deg,#3b4a7a,#c9a07a)"></div>
        <div class="tag"><i></i>NEWS</div>
        <div class="date">Date Posted on 29-08-2014</div>
        <h4>Lorem Ipsum is simply dummy text of the printing and typesetting industry.</h4>
        <p>Lorem Ipsum has been the industry's standard dummy text ever since the 1500s, when an unknown printer took a galley of type and scrambled it to make a type specimen book.</p>
        <a class="btn" href="#">Read More News &gt;&gt;</a>
      </article>
    </div>
  </div>
</section>

<section class="testimonials">
  <h2 class="sec-title">Testimonials</h2>
  <div class="wrap">
    <svg class="side-arrow" style="left:-110px" width="10" height="14" viewBox="0 0 10 14"><path d="M8 1L2 7l6 6" fill="none" stroke="#fff" stroke-width="2"/></svg>
    <svg class="side-arrow" style="right:-110px" width="10" height="14" viewBox="0 0 10 14"><path d="M2 1l6 6-6 6" fill="none" stroke="#fff" stroke-width="2"/></svg>
    <div class="cards3">
      <div class="vid"><div class="thumb" role="img" aria-label="Video testimonial still of a customer" style="background:linear-gradient(135deg,#d8d8d8,#8a6a5a)"><div class="play"><svg width="16" height="18" viewBox="0 0 16 18"><path d="M2 1l13 8-13 8z" fill="#fff"/></svg></div></div><div class="who">Marcus Fell<b>London</b></div></div>
      <div class="vid"><div class="thumb" role="img" aria-label="Video testimonial still of a technician" style="background:linear-gradient(135deg,#1d3f8a,#c9d4e8)"><div class="play"><svg width="16" height="18" viewBox="0 0 16 18"><path d="M2 1l13 8-13 8z" fill="#fff"/></svg></div></div><div class="who">Marcus Fell<b>London</b></div></div>
      <div class="vid"><div class="thumb" role="img" aria-label="Video testimonial still of an engineer" style="background:linear-gradient(135deg,#3b4a7a,#c9a07a)"><div class="play"><svg width="16" height="18" viewBox="0 0 16 18"><path d="M2 1l13 8-13 8z" fill="#fff"/></svg></div></div><div class="who">Marcus Fell<b>London</b></div></div>
    </div>
  </div>
</section>

<section class="blog">
  <h2 class="sec-title">Blog Posts</h2>
  <div class="wrap cards3">
    <article class="post">
      <div class="thumb" role="img" aria-label="Friends sharing a laptop" style="background:linear-gradient(135deg,#c86a8a,#7aa0c8)"><div class="socials"><i></i><i></i><i></i></div></div>
      <h4>Lorem Ipsum is simply dummy text of the printing and typesetting industry.</h4>
      <p>Lorem Ipsum has been the industry's standard dummy text ever since the 1500s, when an unknown printer took a galley of type and scrambled it to make a type specimen book.</p>
      <div class="meta"><a class="btn" href="#">Read More</a><span><svg width="14" height="12" viewBox="0 0 14 12"><path d="M1 1h12v7H6l-3 3V8H1z" fill="#333"/></svg>No Comments</span></div>
    </article>
    <article class="post">
      <div class="thumb" role="img" aria-label="Students working on laptops" style="background:linear-gradient(135deg,#e9e9e9,#d07aa8)"><div class="socials"><i></i><i></i><i></i></div></div>
      <h4>Lorem Ipsum is simply dummy text of the printing and typesetting industry.</h4>
      <p>Lorem Ipsum has been the industry's standard dummy text ever since the 1500s, when an unknown printer took a galley of type and scrambled it to make a type specimen book.</p>
      <div class="meta"><a class="btn" href="#">Read More</a><span><svg width="14" height="12" viewBox="0 0 14 12"><path d="M1 1h12v7H6l-3 3V8H1z" fill="#333"/></svg>No Comments</span></div>
    </article>
    <article class="post">
      <div class="thumb" role="img" aria-label="Child using a tablet" style="background:linear-gradient(135deg,#5a8ac0,#d8c0a8)"><div class="socials"><i></i><i></i><i></i></div></div>
      <h4>Lorem Ipsum is simply dummy text of the printing and typesetting industry.</h4>
      <p>Lorem Ipsum has been the industry's standard dummy text ever since the 1500s, when an unknown printer took a galley of type and scrambled it to make a type specimen book.</p>
      <div class="meta"><a class="btn" href="#">Read More</a><span><svg width="14" height="12" viewBox="0 0 14 12"><path d="M1 1h12v7H6l-3 3V8H1z" fill="#333"/></svg>No Comments</span></div>
    </article>
  </div>
</section>

<section class="messaging">
  <p>Neque porro quisquam est qui dolorem ipsum quia dolor sit amet, consectetur, adipisci velit...</p>
  <a class="btn" href="#">Messaging</a>
</section>

<section class="socialposts">
  <div class="wrap">
    <h2>Latest Social Posts</h2>
    <div class="sp-dots"><i></i><i></i><i></i><i></i></div>
    <div class="sp-post">
      <div class="sp-brand">Northvale</div>
      <div class="sp-body">
        <div class="date">Posted On 29-8-2013</div>
        <p>Lorem Ipsum is simply dummy text of the printing and typesetting industry. Lorem Ipsum has been the industry's standard dummy text ever since the 1500s, when an unknown printer took a galley of type and scrambled it to make a type specimen book.</p>
        <div class="sp-author"><div class="avatar" role="img" aria-label="Author portrait" style="background:linear-gradient(#d8d8d8,#8a7a72)"></div>Marcus Fell,London</div>
      </div>
    </div>
  </div>
</section>

<footer class="footer">
  <div class="wrap">
    <nav>Home<span>|</span>Plans<span>|</span>Benefits<span>|</span>FAQs<span>|</span>About Us</nav>
    <small>© 2014 COMPANY NAME,ALL RIGHTS RESERVED</small>
    <div class="social-dot"></div>
  </div>
</footer>

</body>
</html>
```